Business Cards Needed for Innovative Healthcare Marketing Company

We are a marketing company focused on healthcare. Our company is all about rebranding yourself renewing your image and generating results. The phoenix stands for "reborn" or "rising" which we provide new brands for our clients we take their old brands and renew it with creativity and innovation. I am looking for a business card with color dimension. I have attached an example of a card I think has the look and feel of what I am trying to accomplish. I like that the card example has black and grey font colors, I like the font placement and the small logo, I really like the use of the colors on the right those are the colors of my logo. My logo is phoenix so maybe incorporating flames similar to that design. I would like the back a solid color maybe red with an opaque version of the logo and website. As a marketing company I am always open to creative liberty!

Target Market(s)

Doctors and business professionals.

Industry/Entity Type

Marketing

Contact Information for Business Card

Valcorne Health Care Marketing
Marla Tenwick- CEO
#(512)638-2974
email-marla@valcorne.com
website- valcorne.com

Font styles to use
Sans Serif

Colors
ec1f27
f37122
ffc214
fbed22
fbf289
f04a50

Requirements
Must have
• The logo and required information
Nice to have
• icons by the information
Should not have
• child like font

```html
<!DOCTYPE html>
<html lang="en">
<head>
<meta charset="utf-8">
<title>Valcorne Health Care Marketing – Business Card</title>
<link rel="stylesheet" href="https://fonts.googleapis.com/css2?family=Ubuntu:wght@300;400;500;700&display=swap">
<style>
  :root {
    --backdrop: #2b2b2b;
    --paper: #f1f0ee;
    --paper-edge: #d9d7d3;
    --brand-deep: #8c1b1f;
    --brand-red: #b02a1c;
    --brand-orange: #e0661b;
    --brand-amber: #f08a22;
    --ink-grey: #3a3a3a;
    --rule: #a1343a;
  }
  * { box-sizing: border-box; margin: 0; padding: 0; }
  html, body {
    width: 1200px; height: 1200px; overflow: hidden;
    background: var(--backdrop);
    font-family: "Ubuntu", sans-serif;
  }
  .sheet {
    width: 1200px; height: 1200px;
    display: flex; flex-direction: column; align-items: center; justify-content: center;
    gap: 60px;
  }
  .card {
    position: relative;
    width: 900px; height: 514px;
    background: var(--paper);
    box-shadow: 0 0 0 1px var(--paper-edge);
    overflow: hidden;
  }

  /* Front */
  .front__art { position: absolute; left: 0; top: 0; width: 420px; height: 514px; }
  .brand {
    position: absolute; display: flex; align-items: center; gap: 14px;
    color: var(--brand-deep); font-weight: 300;
  }
  .brand__dot { border-radius: 50%; background: var(--brand-orange); flex: none; }
  .brand__stack { display: flex; flex-direction: column; }
  .brand__name { letter-spacing: 0.06em; line-height: 1; }
  .brand__tag {
    border-top: 1px solid var(--rule); letter-spacing: 0.08em; margin-top: 6px; padding-top: 4px;
  }
  .front .brand { left: 500px; top: 110px; }
  .front .brand__dot { width: 40px; height: 40px; }
  .front .brand__name { font-size: 52px; }
  .front .brand__tag { font-size: 14px; }

  .person { position: absolute; left: 440px; top: 270px; width: 420px; }
  .person__name { font-size: 40px; font-weight: 700; color: var(--brand-deep); }
  .person__role { font-size: 20px; color: var(--ink-grey); margin-top: 2px; }
  .person__rule { height: 1px; background: var(--rule); margin: 14px 0 18px; }
  .contact { list-style: none; font-size: 21px; color: var(--ink-grey); line-height: 1.7; }
  .contact__label { color: var(--brand-deep); font-weight: 700; margin-right: 8px; }
  .contact__sep { color: var(--brand-deep); margin: 0 8px; }

  /* Back */
  .back .brand { left: 50%; top: 50%; transform: translate(-50%, -50%); }
  .back .brand__dot { width: 60px; height: 60px; }
  .back .brand__name { font-size: 76px; }
  .back .brand__tag { font-size: 18px; }
</style>
</head>
<body>
<main class="sheet">

  <section class="card front" aria-label="Business card front">
    <svg class="front__art" viewBox="0 0 420 514" role="img" aria-label="Orange watercolour field with a rising phoenix illustration">
      <defs>
        <linearGradient id="flameField" x1="0" y1="1" x2="1" y2="0">
          <stop offset="0" stop-color="#b8421a"/>
          <stop offset="0.55" stop-color="#d9621c"/>
          <stop offset="1" stop-color="#e57d24"/>
        </linearGradient>
      </defs>
      <path d="M0 0 H400 C380 40 410 80 390 130 C370 180 400 220 360 260 C320 300 300 330 260 360 C230 390 215 440 200 514 H0 Z" fill="url(#flameField)"/>
    </svg>

    <div class="brand">
      <span class="brand__dot"></span>
      <div class="brand__stack">
        <span class="brand__name">VALCORNE</span>
        <span class="brand__tag">HEALTH CARE MARKETING</span>
      </div>
    </div>

    <div class="person">
      <h1 class="person__name">Marla Tenwick</h1>
      <p class="person__role">CEO</p>
      <div class="person__rule"></div>
      <ul class="contact">
        <li><span class="contact__label">T :</span>#(512)638-2974</li>
        <li><span class="contact__label">W :</span>valcorne.com<span class="contact__sep">|</span><span class="contact__label">E:</span>marla@valcorne.com</li>
      </ul>
    </div>
  </section>

  <section class="card back" aria-label="Business card back">
    <div class="brand">
      <span class="brand__dot"></span>
      <div class="brand__stack">
        <span class="brand__name">VALCORNE</span>
        <span class="brand__tag">HEALTH CARE MARKETING</span>
      </div>
    </div>
  </section>

</main>
</body>
</html>
```